Business Card Design needed for start up company Halvora

In need of a new business card designed for a start up company based in Sydney, Halvora is a new start up innovative Company, our mission it to make property accessible for everyday Australian and to become the leading Real Estate platform in Australia. We want it to be fresh and clean.

Industry/Entity Type

Financial

Contact Information for Business Card

Section for Name
Section for Title

HALVORA - The Strength of Pooling
Mobile:
Direct:

Font styles to use
Sans Serif

Colors
33a6d7
0692cd
0255a3
ffffff

Requirements
Must have
• Logo, all business card details

```html
<!DOCTYPE html>
<html lang="en">
<head>
<meta charset="utf-8">
<title>Halvora Business Card</title>
<link href="https://fonts.googleapis.com/css2?family=Roboto:wght@400;500;700&display=swap" rel="stylesheet">
<style>
  :root {
    --page-bg: #c6c6c6;
    --white: #ffffff;
    --azure: #1d99d6;
    --navy: #1d4478;
    --navy-deep: #183a68;
    --navy-light: #214b80;
    --text-soft: #e6f2f9;
    --text-muted: #d8e2ee;
  }
  * { margin: 0; padding: 0; box-sizing: border-box; }
  html, body { width: 1200px; height: 965px; overflow: hidden; }
  body {
    background: var(--page-bg);
    font-family: "Roboto", Arial, sans-serif;
    position: relative;
  }
  .card {
    position: absolute;
    left: 277px;
    width: 648px;
    height: 369px;
    border-radius: 40px;
    overflow: hidden;
  }
  .card-front {
    top: 97px;
    background: linear-gradient(180deg, #f6f6f6 0%, var(--white) 20%, #ececec 60%);
  }
  .card-back {
    top: 502px;
    background: linear-gradient(180deg, var(--navy-light) 0%, var(--navy-deep) 100%);
  }
  .front-bands { position: absolute; inset: 0; }
  .brand-name {
    position: absolute;
    font-weight: 700;
    line-height: 1;
    white-space: nowrap;
  }
  .card-front .brand-name {
    left: 41px; top: 58px;
    font-size: 84px; color: var(--navy);
  }
  .card-back .brand-name {
    left: 0; right: 0; top: 128px;
    text-align: center;
    font-size: 104px; color: var(--white);
  }

  .person { position: absolute; left: 41px; top: 222px; color: var(--white); }
  .person-name { font-size: 20px; font-weight: 700; line-height: 1.1; }
  .person-title { font-size: 15px; color: var(--text-soft); margin-top: 2px; }
  .address {
    position: absolute; left: 40px; top: 309px;
    font-size: 15px; line-height: 19px; color: var(--text-soft);
  }
  .contacts {
    position: absolute; left: 231px; top: 272px;
    list-style: none; color: var(--text-soft); font-size: 15px;
  }
  .contacts li { display: flex; align-items: center; height: 19px; }
  .contacts svg { width: 14px; height: 14px; margin-right: 9px; flex: none; }
  .back-web {
    position: absolute; left: 0; right: 0; top: 336px;
    text-align: center; color: var(--text-muted); font-size: 13px; letter-spacing: 4px;
  }
</style>
</head>
<body>
  <section class="card card-front">
    <svg class="front-bands" viewBox="0 0 648 369" width="648" height="369" aria-hidden="true">
      <defs>
        <linearGradient id="skyFill" x1="0" y1="0" x2="0" y2="1">
          <stop offset="0" stop-color="#2295cc"/>
          <stop offset="1" stop-color="#1c84b8"/>
        </linearGradient>
      </defs>
      <path d="M0 208 L396 208 L418 187 L648 187 L648 369 L0 369 Z" fill="url(#skyFill)"/>
      <path d="M0 190 L411 190 L395 205 L0 205 Z" fill="var(--navy)"/>
    </svg>
    <p class="brand-name">Halvora</p>
    <div class="person">
      <p class="person-name">Daniel Marsh</p>
      <p class="person-title">Managing Director</p>
    </div>
    <p class="address">Here your company or<br>home address</p>
    <ul class="contacts">
      <li>
        <svg viewBox="0 0 14 14"><rect x="1" y="2" width="3" height="11" rx="1" fill="#e6f2f9"/><rect x="5" y="2" width="8" height="11" rx="1" fill="none" stroke="#e6f2f9" stroke-width="1.4"/><rect x="7" y="4" width="4" height="2" fill="#e6f2f9"/><rect x="7" y="8" width="4" height="3" fill="#e6f2f9"/></svg>
        +61 2 8123 4410
      </li>
      <li>
        <svg viewBox="0 0 14 14"><path d="M3 1 L5.5 4 L4.3 5.6 C5 7.4 6.6 9 8.4 9.7 L10 8.5 L13 11 L11.5 13 C6 12.5 1.5 8 1 2.5 Z" fill="#e6f2f9"/></svg>
        +61 412 305 118
      </li>
      <li>
        <svg viewBox="0 0 14 14"><rect x="1" y="3" width="12" height="8" fill="none" stroke="#e6f2f9" stroke-width="1.3"/><path d="M1 3 L7 8 L13 3 M1 11 L5.5 6.8 M13 11 L8.5 6.8" fill="none" stroke="#e6f2f9" stroke-width="1.2"/></svg>
        info@halvora.com
      </li>
      <li>
        <svg viewBox="0 0 14 14"><circle cx="7" cy="7" r="6" fill="none" stroke="#e6f2f9" stroke-width="1.2"/><ellipse cx="7" cy="7" rx="2.6" ry="6" fill="none" stroke="#e6f2f9" stroke-width="1"/><path d="M1 7 H13 M2 4 H12 M2 10 H12" stroke="#e6f2f9" stroke-width="1"/></svg>
        www.halvora.com
      </li>
    </ul>
  </section>

  <section class="card card-back">
    <p class="brand-name">Halvora</p>
    <p class="back-web">www.halvora.com</p>
  </section>
</body>
</html>
```